Web Design For Manufacturing And Outsourcing Company

Pick up the pieces from our previous developer and help us complete our website.

5 pages - Home,Machining,Sourcing,About Us, and Contact

Attached you will find screen shots of previous direction but we're open to new ideas.

We can provide all text and images needed.

Thanks!

Number of Pages Required

5+ page

```html
<!DOCTYPE html>
<html lang="en">
<head>
<meta charset="utf-8">
<title>Kestrel Industries</title>
<link rel="stylesheet" href="https://fonts.googleapis.com/css2?family=Roboto:wght@400;500;700&family=Open+Sans:wght@400;600&display=swap">
<style>
:root{
  --orange:#e8501c;
  --ink:#1d1d1d;
  --grey:#555;
  --dark:#2b2c2f;
  --white:#fff;
  --social:#3d5a98;
}
*{box-sizing:border-box;margin:0;padding:0}
html,body{width:1200px;height:3564px;overflow:hidden;background:var(--white)}
body{font-family:'Open Sans',sans-serif;color:var(--ink);position:relative}
.abs{position:absolute}
.brand{display:flex;align-items:center;gap:12px;font-family:'Roboto',sans-serif;font-weight:500;font-size:17px;white-space:nowrap}
.brand .dot{width:22px;height:22px;background:var(--orange);border-radius:50%}
/* hero */
.hero{left:0;top:0;width:1200px;height:720px;background:radial-gradient(ellipse at 55% 45%,#6b6e72 0%,#3a3c40 45%,#121315 100%)}
.nav{left:0;top:0;width:1200px;height:150px;display:flex;align-items:center;padding:0 165px}
.nav .brand{color:var(--white)}
.menu{display:flex;gap:26px;margin-left:95px;font-family:'Roboto',sans-serif;font-weight:500;font-size:16px;color:var(--white)}
.menu .active{color:var(--orange)}
.hero-title{left:0;top:278px;width:1200px;text-align:center;color:var(--white);font-family:'Roboto',sans-serif;font-weight:700;font-size:38px;line-height:47px}
.arrow{top:292px;width:54px;height:54px;border-radius:50%;background:rgba(255,255,255,.35);display:flex;align-items:center;justify-content:center}
.badge{left:566px;top:676px;width:68px;height:68px;border-radius:50%;background:var(--white);display:flex;align-items:center;justify-content:center;box-shadow:0 2px 6px rgba(0,0,0,.15)}
.badge i{width:26px;height:26px;border-radius:50%;background:var(--orange)}
/* about */
.about{left:0;top:720px;width:1200px;height:640px;background:linear-gradient(#fff 0%,#f5f5f5 60%,#e9e9e9 100%)}
.h2{font-family:'Roboto',sans-serif;font-weight:700;font-size:36px;text-align:center;width:1200px;left:0}
.h3o{font-family:'Roboto',sans-serif;font-weight:700;font-size:22px;color:var(--orange);text-align:center;width:1200px;left:0}
.policy{left:240px;top:880px;width:720px;text-align:center;font-size:15.5px;line-height:29px;color:#333}
.values-title{left:0;top:1032px;width:1200px;text-align:center;font-family:'Roboto',sans-serif;font-weight:700;font-size:22px}
.value{top:1098px;width:260px;display:flex;gap:14px}
.value svg{flex:none}
.value h4{font-family:'Roboto',sans-serif;font-weight:700;font-size:16px;color:var(--orange);margin-bottom:6px}
.value p{font-size:13.5px;line-height:20px;color:#555}
.value b{display:block;margin-top:14px;font-size:12.5px;color:#444;font-family:'Roboto',sans-serif}
/* sourcing */
.sourcing-bg{left:0;top:1320px;width:1200px;height:860px}
.sourcing h2{color:var(--white)}
.lead-w{color:var(--white);font-size:19px;text-align:center;width:1200px;left:0}
.intro{font-size:13.5px;line-height:21px}
.feature{display:flex;gap:22px;width:420px}
.feature svg{flex:none}
.feature h4{font-family:'Roboto',sans-serif;font-weight:700;font-size:21px;margin-bottom:4px}
.feature p{font-size:14px;line-height:21px}
.sourcing .feature,.sourcing .intro{color:var(--white)}
.photo-frame{left:622px;top:1520px;width:432px;height:506px;border:1.5px solid rgba(255,255,255,.8)}
.photo{position:absolute}
/* machining */
.machining .feature h4{font-weight:400;font-size:21px;color:var(--ink)}
.machining .feature p{color:#444}
.machining .intro{color:#444}
/* cta */
.cta{left:0;top:2890px;width:1200px;height:520px}
.cta-title{left:0;top:3102px;width:1200px;text-align:center;color:var(--white);font-family:'Roboto',sans-serif;font-size:31px;line-height:45px}
.btn{left:510px;top:3208px;width:200px;height:50px;background:var(--orange);color:var(--white);font-family:'Roboto',sans-serif;font-weight:700;font-size:17px;display:flex;align-items:center;justify-content:center;border-radius:3px}
/* footer */
.footer .brand{color:var(--ink)}
.fmenu{left:402px;top:3456px;display:flex;gap:18px;font-family:'Roboto',sans-serif;font-weight:500;font-size:15px}
.copy{left:402px;top:3488px;font-family:'Roboto',sans-serif;font-size:12.5px;color:#555}
.social{top:3450px;width:30px;height:30px;border-radius:50%;background:var(--social)}
</style>
</head>
<body>

<section class="hero abs" role="img" aria-label="Close-up photo of precision machined metal parts"></section>
<header class="nav abs">
  <div class="brand"><i class="dot"></i>Kestrel Industries</div>
  <nav class="menu"><span class="active">HOME</span><span>MACHINING CAPABILITIES</span><span>SOURCING</span><span>CONTACT US</span></nav>
</header>
<h1 class="hero-title abs">A SINGLE POINT OF CONTACT FOR ALL<br>YOUR PROCUREMENT NEEDS</h1>
<div class="arrow abs" style="left:96px"><svg width="18" height="18" viewBox="0 0 18 18"><path d="M12 2 5 9l7 7" fill="none" stroke="#222" stroke-width="2.5"/></svg></div>
<div class="arrow abs" style="left:1046px"><svg width="18" height="18" viewBox="0 0 18 18"><path d="M6 2l7 7-7 7" fill="none" stroke="#222" stroke-width="2.5"/></svg></div>
<svg class="abs" style="left:0;top:500px" width="1200" height="230" viewBox="0 0 1200 230">
  <path d="M0 200 C400 210 900 150 1200 20 L1200 230 L0 230Z" fill="var(--orange)"/>
  <path d="M0 205 C420 205 900 175 1200 75 L1200 230 L0 230Z" fill="#fff"/>
</svg>

<section class="about abs"></section>
<div class="badge abs"><i></i></div>
<h2 class="h2 abs" style="top:778px">ABOUT US</h2>
<h3 class="h3o abs" style="top:842px">QUALITY POLICY</h3>
<p class="policy abs">We are committed to consistently exceeding customer expectations by providing products, services and sourcing solutions of the highest standard of quality. With our streamlined processes our method is efficient, provides value and ensures on time delivery. Our success isbased on continuously improving the efficiencies and effectiveness of our products</p>
<h3 class="values-title abs">CORE VALUES</h3>

<div class="value abs" style="left:192px">
  <svg width="52" height="52" viewBox="0 0 52 52" fill="none" stroke="var(--orange)" stroke-width="2.5"><circle cx="14" cy="12" r="6"/><circle cx="38" cy="12" r="6"/><circle cx="26" cy="20" r="6"/><path d="M4 38c0-8 5-14 10-14M48 38c0-8-5-14-10-14M14 46c0-9 5-16 12-16s12 7 12 16Z"/></svg>
  <div><h4>TEAMWORK</h4><p>We are one company, one team. We understand when we work together we work smarter and not harder.</p><b>READ MORE</b></div>
</div>
<div class="value abs" style="left:462px">
  <svg width="62" height="52" viewBox="0 0 62 52" fill="none" stroke="var(--orange)" stroke-width="2.5"><path d="M4 14l12-8 10 6 10-6 12 8 8 14-20 18-10-8-10 6L4 28Z"/><path d="M22 26l10 8M28 20l12 10"/></svg>
  <div><h4>RESPECT</h4><p>We are one company, one team. We understand when we work together we work smarter and not harder.</p><b>READ MORE</b></div>
</div>
<div class="value abs" style="left:790px">
  <svg width="52" height="52" viewBox="0 0 52 52" fill="none" stroke="var(--orange)" stroke-width="2.5"><path d="M12 26V8h6v14M18 6h6v16M24 8h6v14M30 12h6v16c0 10-6 18-14 18s-10-6-10-14"/></svg>
  <div><h4>GRATITUDE</h4><p>We appreciate where we have come from and the opportunities we are given to continue our journey.</p><b>READ MORE</b></div>
</div>

<svg class="sourcing-bg abs" viewBox="0 0 1200 860" preserveAspectRatio="none">
  <path d="M0 120 C300 40 800 20 1200 10 L1200 820 C900 790 600 820 0 820Z" fill="#3a3a3c"/>
  <path d="M0 135 C300 60 800 40 1200 32 L1200 760 C900 800 500 810 0 820Z" fill="var(--orange)"/>
  <path d="M780 845 C950 830 1100 790 1200 700 L1200 760 C1100 810 950 840 780 845Z" fill="#3a3a3c"/>
</svg>
<section class="sourcing">
  <h2 class="h2 abs" style="top:1394px">SOURCING</h2>
  <p class="lead-w abs" style="top:1444px">Minimizing Costs by Providing Specific Sourcing Solutions for Each Individual Job!</p>
  <p class="intro abs" style="left:168px;top:1527px;width:430px">Pellentesque faucibus Ut accumsan ultricies elit Maecenas at justo id velit placerat molestie Donec dictum lectus non odio Cras a ante vitae enim iaculis aliquam Mauris nunc quam venenatis nec</p>
  <div class="feature abs" style="left:168px;top:1620px">
    <svg width="56" height="56" viewBox="0 0 56 56" fill="none" stroke="#fff" stroke-width="2.2"><circle cx="28" cy="28" r="20"/><circle cx="28" cy="28" r="8"/><path d="M28 2v8M28 46v8M2 28h8M46 28h8"/></svg>
    <div><h4>Vetting</h4><p>Pellentesque faucibus Ut accumsan ultricies elit Maecenas at justo id velit placerat molestie</p></div>
  </div>
  <div class="feature abs" style="left:168px;top:1730px">
    <svg width="56" height="56" viewBox="0 0 56 56" fill="none" stroke="#fff" stroke-width="2.2"><circle cx="28" cy="28" r="22" stroke-dasharray="4 3"/><path d="M28 14l4 9 10 1-8 6 3 10-9-5-9 5 3-10-8-6 10-1Z"/></svg>
    <div><h4>Quality</h4><p>Pellentesque faucibus Ut accumsan ultricies elit Maecenas at justo id velit placerat molestie</p></div>
  </div>
  <div class="feature abs" style="left:168px;top:1840px">
    <svg width="56" height="56" viewBox="0 0 56 56" fill="none" stroke="#fff" stroke-width="2.2"><circle cx="28" cy="28" r="22"/><circle cx="28" cy="28" r="14"/><circle cx="28" cy="28" r="5"/></svg>
    <div><h4>Process</h4><p>Pellentesque faucibus Ut accumsan ultricies elit Maecenas at justo id velit placerat molestie</p></div>
  </div>
  <div class="feature abs" style="left:168px;top:1950px">
    <svg width="56" height="56" viewBox="0 0 56 56" fill="none" stroke="#fff" stroke-width="2.2"><rect x="6" y="8" width="44" height="30"/><path d="M12 32l10-10 8 6 14-14M28 38l-8 14M28 38l8 14"/></svg>
    <div><h4>Benefits</h4><p>Pellentesque faucibus Ut accumsan ultricies elit Maecenas at justo id velit placerat molestie</p></div>
  </div>
  <div class="photo-frame abs"></div>
  <div class="photo" role="img" aria-label="Business silhouettes shaking hands over a digital network graphic" style="left:641px;top:1520px;width:408px;height:490px;background:linear-gradient(160deg,#3f8a86 0%,#14525a 50%,#0b2a35 100%)"></div>
</section>

<section class="machining">
  <h2 class="h2 abs" style="top:2206px;font-size:34px">MACHINING</h2>
  <p class="abs" style="left:0;top:2256px;width:1200px;text-align:center;font-family:'Roboto',sans-serif;font-size:22px">Our In-house capablities</p>
  <div class="photo" role="img" aria-label="CNC lathe cutting a metal part" style="left:157px;top:2333px;width:411px;height:494px;background:linear-gradient(135deg,#cbd6de 0%,#6f8393 40%,#2a3540 100%)"></div>
  <p class="intro abs" style="left:606px;top:2324px;width:460px">Pellentesque faucibus Ut accumsan ultricies elit Maecenas at justo id velit placerat molestie Donec dictum lectus non odio Cras a ante vitae enim iaculis aliquam Mauris nunc quam venenatis nec</p>
  <div class="feature abs" style="left:606px;top:2412px;width:470px">
    <svg width="60" height="56" viewBox="0 0 60 56" fill="none" stroke="var(--orange)" stroke-width="2.2"><rect x="4" y="40" width="28" height="10"/><path d="M14 40V20l18-10 10 8M42 18l8 8"/><circle cx="14" cy="20" r="4"/><rect x="40" y="30" width="16" height="20"/></svg>
    <div><h4>Multiple Axis Equipment</h4><p>Pellentesque faucibus Ut accumsan ultricies elit Maecenas at justo id velit placerat molestie Donec dictum</p></div>
  </div>
  <div class="feature abs" style="left:606px;top:2520px;width:470px">
    <svg width="60" height="56" viewBox="0 0 60 56" fill="none" stroke="var(--orange)" stroke-width="2.2"><rect x="6" y="6" width="48" height="40"/><path d="M6 16h48M16 26h28M16 34h20M20 46l-4 6h28l-4-6"/></svg>
    <div><h4>Tolerances of =/.0001</h4><p>Pellentesque faucibus Ut accumsan ultricies elit Maecenas at justo id velit placerat molestie Donec dictum</p></div>
  </div>
  <div class="feature abs" style="left:606px;top:2628px;width:470px">
    <svg width="60" height="56" viewBox="0 0 60 56" fill="none" stroke="var(--orange)" stroke-width="2.2"><rect x="18" y="2" width="24" height="10"/><path d="M22 12v8h16v-8M20 24h20M22 30h16M24 36h12M26 42h8M30 42v12"/></svg>
    <div><h4>Custom Built Fixtures</h4><p>Pellentesque faucibus Ut accumsan ultricies elit Maecenas at justo id velit placerat molestie Donec dictum</p></div>
  </div>
  <div class="feature abs" style="left:606px;top:2732px;width:470px">
    <svg width="60" height="56" viewBox="0 0 60 56" fill="none" stroke="var(--orange)" stroke-width="2.2"><rect x="6" y="12" width="48" height="38"/><circle cx="30" cy="31" r="12"/><path d="M30 24v7l5 4M16 4v8M44 4v8"/></svg>
    <div><h4>Prototypes to Production Runs</h4><p>Pellentesque faucibus Ut accumsan ultricies elit Maecenas at justo id velit placerat molestie Donec dictum</p></div>
  </div>
</section>

<section class="cta abs" role="img" aria-label="Dark photo of a machined metal part on a lathe" style="background:radial-gradient(ellipse at 30% 55%,#5b5e63 0%,#2e3034 55%,#17181a 100%)"></section>
<svg class="abs" style="left:0;top:2880px" width="1200" height="540" viewBox="0 0 1200 540" preserveAspectRatio="none">
  <path d="M0 0 H1200 V70 C900 20 400 20 0 80Z" fill="#fff"/>
  <path d="M0 80 C400 20 900 20 1200 70 L1200 84 C900 40 400 40 0 96Z" fill="var(--orange)"/>
  <path d="M0 420 C300 500 800 520 1200 470 L1200 540 L0 540Z" fill="var(--orange)"/>
  <path d="M0 440 C300 520 800 530 1200 490 L1200 540 L0 540Z" fill="#fff"/>
</svg>
<div class="abs" style="left:588px;top:3034px;width:24px;height:24px;border-radius:50%;background:#fff"></div>
<h2 class="cta-title abs">CONTACT US TODAY WITH YOUR MACHINING<br>OR SOURCING NEEDS!</h2>
<div class="btn abs">GET IN TOUCH</div>

<footer class="footer">
  <div class="brand abs" style="left:142px;top:3458px"><i class="dot"></i>Kestrel Industries</div>
  <nav class="fmenu abs"><span>HOME</span><span>MACHINING</span><span>CAPABILITIES</span><span>SOURCING</span><span>CONTACT US</span></nav>
  <p class="copy abs">© 2019 Company Name &nbsp;All right reserved</p>
  <span class="social abs" style="left:928px"></span>
  <span class="social abs" style="left:964px"></span>
  <span class="social abs" style="left:1000px"></span>
  <span class="social abs" style="left:1036px"></span>
</footer>

</body>
</html>
```